Antiseptic products for Verolin East Africa

I need several antiseptic product designs for topical solutions such as surgical spirit, methylated spirit, hand sanitizer, calamine lotion, povidone solution, glycerine, povidone mouthwash, chlorhexidine solution, and sodium hypochlorite solution.

KINDLY START WITH THE HAND SANITIZER DESIGN, URGENT.

Target Market(s)

International market

Industry/Entity Type

Pharmaceutical

Font styles to use
Serif
Script

Colors
33a6d7
3277b5
0758a5
7651a1
886aae
e34197
e667a6
f78f20

Requirements
Must have
• Elegant designs, writtings to appear as they are. safety symbols to appear such as flammable or corrosive.
Nice to have
• Attractive colours but keep it simple and classy.

```html
<!DOCTYPE html>
<html lang="en">
<head>
<meta charset="utf-8">
<title>Purelo Hand Sanitizer Label</title>
<link rel="stylesheet" href="https://fonts.googleapis.com/css2?family=Montserrat:wght@500;700&family=Lora:wght@500&display=swap">
<style>
  :root {
    --backdrop: #eef2f6;
    --label: #ffffff;
    --ink: #0758a5;
    --panel: #3277b5;
    --panel-text: #ffffff;
    --accent: #33a6d7;
    --hazard-frame: #e34197;
    --hazard-flame: #1a1a1a;
  }
  html, body {
    margin: 0;
    padding: 0;
    width: 980px;
    height: 1200px;
    overflow: hidden;
    background: var(--backdrop);
  }
  .canvas {
    position: relative;
    width: 980px;
    height: 1200px;
  }
  .label {
    position: absolute;
    left: 98px;
    top: 144px;
    width: 784px;
    height: 912px;
    background: var(--label);
    border-radius: 30px;
    box-shadow: 0 6px 24px rgba(7, 88, 165, 0.12);
    color: var(--ink);
  }
  .product-name {
    position: absolute;
    left: 78px;
    top: 86px;
    margin: 0;
    font-family: 'Montserrat', sans-serif;
    font-weight: 700;
    font-size: 100px;
    line-height: 110px;
    letter-spacing: -3px;
    text-transform: uppercase;
  }
  .volume {
    position: absolute;
    left: 80px;
    top: 330px;
    margin: 0;
    font-family: 'Montserrat', sans-serif;
    font-weight: 500;
    font-size: 46px;
    letter-spacing: 0.5px;
  }
  .maker {
    position: absolute;
    right: 24px;
    top: 24px;
    width: 130px;
    text-align: center;
  }
  .maker-dot {
    display: block;
    margin: 0 auto 8px;
  }
  .maker-name {
    font-family: 'Lora', serif;
    font-weight: 500;
    font-size: 19px;
    letter-spacing: 1.5px;
    text-transform: uppercase;
    color: var(--accent);
  }
  .hazard {
    position: absolute;
    right: 44px;
    top: 290px;
  }
  .brand-panel {
    position: absolute;
    left: 30px;
    top: 427px;
    width: 724px;
    height: 442px;
    background: var(--panel);
    border-radius: 26px;
    display: flex;
    align-items: center;
    justify-content: center;
  }
  .brand-name {
    margin: 40px 0 0;
    color: var(--panel-text);
    font-family: 'Lora', serif;
    font-weight: 500;
    font-size: 150px;
  }
</style>
</head>
<body>
  <main class="canvas">
    <section class="label">
      <div class="maker">
        <svg class="maker-dot" width="70" height="70" viewBox="0 0 70 70" aria-hidden="true">
          <circle cx="35" cy="35" r="31" fill="none" stroke="var(--accent)" stroke-width="4"/>
        </svg>
        <span class="maker-name">Verolin</span>
      </div>
      <h1 class="product-name">Hand<br>Sanitizer</h1>
      <p class="volume">100 ml / 3.5fl.oz.</p>
      <svg class="hazard" width="110" height="110" viewBox="0 0 110 110" role="img" aria-label="Flammable warning symbol">
        <rect x="23" y="23" width="64" height="64" rx="4" transform="rotate(45 55 55)" fill="#ffffff" stroke="var(--hazard-frame)" stroke-width="7"/>
        <path d="M55 28 C62 40 70 46 68 60 C67 70 61 76 55 76 C48 76 42 70 42 61 C42 53 47 49 49 43 C51 49 53 51 55 52 C57 45 56 36 55 28 Z" fill="var(--hazard-flame)"/>
        <rect x="38" y="79" width="34" height="4" fill="var(--hazard-flame)"/>
      </svg>
      <div class="brand-panel">
        <p class="brand-name">Purelo</p>
      </div>
    </section>
  </main>
</body>
</html>
```